Marlow Dermal Studio - Business Banner with Brand Elements

Design:
• We would like to get a creative design for a wide banner that will go outside our medical spa clinic location. We need a designer to make a simple yet colorful and high-quality design layout. We want this banner to be eye-catching and to communicate the services we offer at our business: Laser Hair Removal | Veluxin | Lip Filler.

Requirements:
• We would like the banner to include our companies information which is the following:

Logo
“Refresh Your Skin”
Laser Hair Removal | Veluxin | Lip Filler
(520) 867-2291
www.MarlowDermalStudio.com

Colors:
• Our business colors are orange, a hint of black and white, but mostly peach/orange tones. (Orange: #f78f20 , White: #ffffff)

Fonts:
• Josefins Sans Bold & Lato

Content and images can be located here:
https://files.quibbleshare.com/share/folders/7tKwP3zRa9_LmQxVb2nD5yHc04EeJuFs8?mode=viewing

The following will give you an idea of our brand presentation:
• Our website is: www.MarlowDermalStudio.com
• Our Pictavo; @marlowdermalstudio
• Our Lumora: www.lumoranet.com/marlowdermalstudio

Target Market(s)
• Women 25 - 45

Industry/Entity Type
• Beauty

```html
<!DOCTYPE html>
<html lang="en">
<head>
<meta charset="utf-8">
<title>Marlow Dermal Studio – Banner Options</title>
<link href="https://fonts.googleapis.com/css2?family=Josefin+Sans:wght@700&family=Lato:wght@400;700&display=swap" rel="stylesheet">
<style>
  :root {
    --orange: #f78f20;
    --white: #ffffff;
    --black: #111111;
    --stage: #8e8e8e;
    --mint: #dce5e3;
    --tan: #c7ab8b;
  }
  * { box-sizing: border-box; margin: 0; padding: 0; }
  html, body { width: 1151px; height: 1200px; overflow: hidden; background: var(--stage); }
  .stage { position: relative; width: 1151px; height: 1200px; }

  .banner {
    position: absolute; left: 68px; width: 1015px; height: 338px; overflow: hidden;
    box-shadow: 0 4px 10px rgba(0,0,0,.35);
  }
  .banner--mint { top: 52px; background: var(--mint); }
  .banner--tan { top: 431px; background: var(--tan); }
  .banner--orange { top: 810px; background: var(--orange); }

  .photo { position: absolute; top: 0; bottom: 0; }
  .banner--mint .photo {
    left: 540px; right: 0;
    background:
      linear-gradient(to right, var(--mint) 0%, rgba(220,229,227,0) 30%),
      linear-gradient(180deg, #d6e8f1 0%, #a9cad8 38%, #e6ecec 62%, #e8dfd2 100%);
  }
  .banner--tan .photo {
    left: 500px; right: 0;
    background:
      linear-gradient(to right, var(--tan) 0%, rgba(199,171,139,0) 28%),
      radial-gradient(ellipse at 60% 55%, #b98a6a 0%, #c9a88a 45%, #c4a585 100%);
  }
  .banner--orange .photo {
    left: 0; width: 560px;
    background:
      linear-gradient(to right, rgba(255,255,255,0) 55%, #f6f4ef 90%),
      linear-gradient(180deg, #a9b1a6 0%, #7f8f72 30%, #c9a36a 70%, #e9a33c 100%);
  }
  .edge-curve { position: absolute; left: 0; top: 0; }
  .arc { position: absolute; left: 0; top: 0; }

  .brand { position: absolute; display: flex; align-items: center; gap: 12px; }
  .brand__mark { width: 56px; height: 56px; border-radius: 50%; background: var(--orange); flex: none; }
  .brand__name {
    font-family: 'Josefin Sans', sans-serif; font-weight: 700; font-size: 28px;
    color: var(--black); line-height: 1; padding-top: 4px; white-space: nowrap;
  }
  .banner--orange .brand__mark { background: var(--white); }
  .banner--orange .brand__name { color: var(--white); }

  .headline {
    position: absolute; font-family: 'Josefin Sans', sans-serif; font-weight: 700;
    font-size: 43px; line-height: 1; letter-spacing: 1px; color: var(--black); white-space: nowrap;
  }
  .headline__accent { color: var(--orange); }
  .banner--orange .headline { font-size: 35px; }

  .services {
    position: absolute; background: var(--orange); color: var(--white);
    font-family: 'Lato', sans-serif; font-weight: 700; font-size: 22px;
    display: flex; align-items: center; justify-content: center; white-space: nowrap;
  }
  .banner--orange .services { background: var(--black); font-size: 19px; }

  .contact { position: absolute; font-family: 'Lato', sans-serif; color: #222; }
  .contact__row { display: flex; align-items: center; height: 32px; font-size: 22px; white-space: nowrap; }
  .contact__icon { width: 24px; height: 24px; margin-right: 18px; flex: none; }
  .banner--orange .contact__row { font-size: 18px; height: 29px; }
  .banner--orange .contact__icon { width: 20px; height: 20px; margin-right: 15px; }

  .social { display: flex; gap: 6px; margin-left: 22px; flex: none; }
  .social__pill {
    height: 34px; padding: 0 10px; border: 2px solid var(--black); border-radius: 17px;
    background: var(--white); font-family: 'Lato', sans-serif; font-weight: 700; font-size: 12px;
    color: var(--black); display: flex; align-items: center;
  }
  .banner--orange .social { margin-left: 14px; gap: 5px; }
  .banner--orange .social__pill { height: 30px; padding: 0 7px; font-size: 11px; }
</style>
</head>
<body>
<div class="stage">

  <!-- Option 1: mint -->
  <section class="banner banner--mint">
    <div class="photo" role="img" aria-label="Smiling woman with windswept hair on a sunny beach"></div>
    <div class="brand" style="left:46px;top:34px;">
      <span class="brand__mark"></span><span class="brand__name">Marlow Dermal Studio</span>
    </div>
    <h1 class="headline" style="left:46px;top:145px;">REFRESH <span class="headline__accent">YOUR SKIN</span></h1>
    <div class="services" style="left:46px;top:197px;width:443px;height:35px;">Laser Hair Removal | Veluxin | Lip Filler</div>
    <div class="contact" style="left:46px;top:251px;">
      <div class="contact__row"><svg class="contact__icon" viewBox="0 0 24 24"><path fill="#f78f20" d="M6.6 2.5l3 3.3-1.9 2.6c1.2 2.8 3.3 5 6 6.2l2.6-1.9 3.3 3-1.8 3.5C10.5 19.4 4.5 13.4 3.2 4.4z"/></svg>(520) 867-2291</div>
      <div class="contact__row"><svg class="contact__icon" viewBox="0 0 24 24" fill="none" stroke="#f78f20" stroke-width="2"><circle cx="12" cy="12" r="10"/><ellipse cx="12" cy="12" rx="4.5" ry="10"/><path d="M2 12h20M4 7h16M4 17h16"/></svg>www.MarlowDermalStudio.com
        <div class="social"><span class="social__pill">Lumora</span><span class="social__pill">Pictavo</span></div>
      </div>
    </div>
  </section>

  <!-- Option 2: tan -->
  <section class="banner banner--tan">
    <div class="photo" role="img" aria-label="Three women with glowing skin posed close together"></div>
    <svg class="edge-curve" width="30" height="338" viewBox="0 0 30 338"><path d="M0 0 Q 30 169 0 338 Z" fill="#f78f20"/></svg>
    <div class="brand" style="left:54px;top:38px;">
      <span class="brand__mark"></span><span class="brand__name">Marlow Dermal Studio</span>
    </div>
    <h1 class="headline" style="left:53px;top:146px;">REFRESH <span class="headline__accent">YOUR SKIN</span></h1>
    <div class="services" style="left:54px;top:203px;width:410px;height:32px;">Laser Hair Removal | Veluxin | Lip Filler</div>
    <div class="contact" style="left:54px;top:258px;">
      <div class="contact__row"><svg class="contact__icon" viewBox="0 0 24 24"><path fill="#111" d="M6.6 2.5l3 3.3-1.9 2.6c1.2 2.8 3.3 5 6 6.2l2.6-1.9 3.3 3-1.8 3.5C10.5 19.4 4.5 13.4 3.2 4.4z"/></svg>(520) 867-2291</div>
      <div class="contact__row"><svg class="contact__icon" viewBox="0 0 24 24" fill="none" stroke="#111" stroke-width="2"><circle cx="12" cy="12" r="10"/><ellipse cx="12" cy="12" rx="4.5" ry="10"/><path d="M2 12h20M4 7h16M4 17h16"/></svg>www.MarlowDermalStudio.com
        <div class="social"><span class="social__pill">Lumora</span><span class="social__pill">Pictavo</span></div>
      </div>
    </div>
  </section>

  <!-- Option 3: orange -->
  <section class="banner banner--orange">
    <div class="photo" role="img" aria-label="Smiling woman in an orange top on a sunny city street"></div>
    <svg class="arc" width="1015" height="338" viewBox="0 0 1015 338">
      <path d="M0 0 Q 26 169 0 338 Z" fill="#f78f20"/>
      <path d="M532 0 Q 420 169 532 338" fill="none" stroke="#f78f20" stroke-width="6"/>
      <path d="M553 0 Q 440 169 553 338 L1015 338 L1015 0 Z" fill="#f78f20"/>
      <path d="M553 0 Q 440 169 553 338" fill="none" stroke="#ffffff" stroke-width="9"/>
    </svg>
    <div class="brand" style="left:592px;top:28px;">
      <span class="brand__mark"></span><span class="brand__name">Marlow Dermal Studio</span>
    </div>
    <h1 class="headline" style="left:590px;top:142px;">REFRESH YOUR SKIN</h1>
    <div class="services" style="left:591px;top:198px;width:364px;height:29px;">Laser Hair Removal | Veluxin | Lip Filler</div>
    <div class="contact" style="left:591px;top:255px;">
      <div class="contact__row"><svg class="contact__icon" viewBox="0 0 24 24"><path fill="#111" d="M6.6 2.5l3 3.3-1.9 2.6c1.2 2.8 3.3 5 6 6.2l2.6-1.9 3.3 3-1.8 3.5C10.5 19.4 4.5 13.4 3.2 4.4z"/></svg>(520) 867-2291</div>
      <div class="contact__row"><svg class="contact__icon" viewBox="0 0 24 24" fill="none" stroke="#111" stroke-width="2"><circle cx="12" cy="12" r="10"/><ellipse cx="12" cy="12" rx="4.5" ry="10"/><path d="M2 12h20M4 7h16M4 17h16"/></svg>www.MarlowDermalStudio.com
        <div class="social"><span class="social__pill">Lumora</span><span class="social__pill">Pictavo</span></div>
      </div>
    </div>
  </section>

</div>
</body>
</html>
```